Maple Roster Business Card for recruitment company

We are looking for a Business Card Design that incorporates our personal details and our busines name and logo. We are a specialized search consultancy that recruit Property and Construction professionals.
We would like a business card that stands out and is appealing to the Construction and Property industry as well.

Target Market(s)

people in the construction and property industry

Contact Information for Business Card

Business Name and logo

Font styles to use
Serif

Colors
0094D4
00A9DD
6FCCEA
C7EBF8
E9F6FB

Requirements
Must have
• Business name and logo as well as contact details
Should not have
• No photos of us please

```html
<!DOCTYPE html>
<html lang="en">
<head>
<meta charset="utf-8">
<title>Maple Roster – Business Card</title>
<link rel="stylesheet" href="https://fonts.googleapis.com/css2?family=Montserrat:wght@700&family=Questrial&display=swap">
<style>
  :root {
    --backdrop: #2a2a2a;
    --card-white: #ffffff;
    --card-fade: #f1f1f1;
    --navy: #0a3a52;
    --navy-deep: #062d42;
    --navy-light: #0e4560;
    --text-grey: #454545;
    --band-text: #ffffff;
  }
  * { margin: 0; padding: 0; box-sizing: border-box; }
  html, body {
    width: 1200px;
    height: 732px;
    overflow: hidden;
    background: var(--backdrop);
  }
  .canvas {
    position: relative;
    width: 1200px;
    height: 732px;
  }
  .card {
    position: absolute;
    top: 242px;
    width: 436px;
    height: 248px;
    box-shadow: 0 6px 14px rgba(0,0,0,0.45);
    overflow: hidden;
  }
  .card--front {
    left: 144px;
    background: linear-gradient(160deg, var(--card-white) 40%, var(--card-fade) 100%);
    font-family: "Questrial", sans-serif;
  }
  .card--back {
    left: 621px;
  }
  .wordmark {
    position: absolute;
    top: 16px;
    left: 0;
    width: 100%;
    text-align: center;
    font-family: "Questrial", sans-serif;
    font-size: 34px;
    line-height: 38px;
    letter-spacing: 1px;
    color: var(--navy);
  }
  .person {
    position: absolute;
    right: 200px;
    top: 102px;
    text-align: right;
    white-space: nowrap;
  }
  .person__name {
    font-family: "Montserrat", sans-serif;
    font-weight: 700;
    font-size: 16.5px;
    line-height: 20px;
    color: var(--navy);
  }
  .person__role {
    font-size: 13px;
    line-height: 16px;
    color: var(--text-grey);
  }
  .divider {
    position: absolute;
    left: 244px;
    top: 104px;
    width: 1px;
    height: 38px;
    background: var(--text-grey);
  }
  .contact {
    position: absolute;
    left: 254px;
    top: 102px;
    list-style: none;
    font-size: 12.5px;
    line-height: 14.2px;
    color: var(--text-grey);
    white-space: nowrap;
  }
  .contact__label {
    display: inline-block;
    width: 19px;
    font-family: "Montserrat", sans-serif;
    font-weight: 700;
    font-size: 11px;
    color: var(--navy);
  }
  .location-band {
    position: absolute;
    left: 0;
    bottom: 0;
    width: 100%;
    height: 46px;
    background: var(--navy);
    color: var(--band-text);
    font-size: 12.5px;
    line-height: 46px;
    text-align: center;
    letter-spacing: 0.3px;
  }
  .back-pattern {
    position: absolute;
    inset: 0;
    background: linear-gradient(135deg, var(--navy-light) 0%, var(--navy) 45%, var(--navy-deep) 100%);
  }
  .back-name {
    position: absolute;
    top: 0;
    left: 0;
    width: 100%;
    height: 100%;
    display: flex;
    align-items: center;
    justify-content: center;
    font-family: "Questrial", sans-serif;
    font-size: 24px;
    letter-spacing: 1px;
    color: var(--band-text);
  }
</style>
</head>
<body>
<main class="canvas">
  <section class="card card--front" aria-label="Business card front">
    <div class="wordmark">MAPLE ROSTER</div>
    <div class="person">
      <div class="person__name">Clara Whitmore</div>
      <div class="person__role">Director&nbsp; |&nbsp; Senior Search Consultant</div>
    </div>
    <div class="divider"></div>
    <ul class="contact">
      <li><span class="contact__label">T:</span> +64 27 555 0142</li>
      <li><span class="contact__label">E:</span> clara@mapleroster.nz</li>
      <li><span class="contact__label">W:</span>www.mapleroster.nz</li>
    </ul>
    <div class="location-band">Hamilton, New Zealand</div>
  </section>

  <section class="card card--back" aria-label="Business card back">
    <div class="back-pattern" role="img" aria-label="Faint repeating pattern of the brand symbol on deep navy"></div>
    <div class="back-name">MAPLE ROSTER</div>
  </section>
</main>
</body>
</html>
```